Marlowe Group needs a business card

I would like the card to be simple but modern and elegant.
I like black and white.
or black and gold.
we are a private finance lender and also are involved in property and property developments.

please look at the business card photos i provided i would like M.G only one one side and all the other details on the other side use fonts that tie in with my theme.

Industry/Entity Type

Finance

Contact Information for Business Card

Marlowe Group (M.G) Daniel Marlowe M: 0413586207 E: danmarl@inboxmail.test

Font styles to use
Other font styles liked:
• Use fonts that would reflect our business

Colors
000000
ffffff

Requirements
Must have
• one side of details
• other side has either M.G or Marlowe Group like in the photos provided

```html
<!DOCTYPE html>
<html lang="en">
<head>
<meta charset="utf-8">
<title>Marlowe Group – Business Card</title>
<link rel="stylesheet" href="https://fonts.googleapis.com/css2?family=Open+Sans:wght@400;700;800&display=swap">
<style>
  :root {
    --backdrop: #3a3431;
    --card: #141618;
    --card-edge: #0c0d0e;
    --ink: #ffffff;
    --ink-soft: #e4e4e4;
  }
  * { margin: 0; padding: 0; box-sizing: border-box; }
  html, body {
    width: 1200px;
    height: 769px;
    overflow: hidden;
    background: var(--backdrop);
    font-family: "Open Sans", Arial, sans-serif;
  }
  .sheet {
    width: 1200px;
    height: 769px;
    display: flex;
    align-items: center;
    justify-content: center;
    gap: 60px;
  }
  .card {
    position: relative;
    width: 510px;
    height: 291px;
    background: var(--card);
    border: 1px solid var(--card-edge);
    box-shadow: 0 14px 30px rgba(0, 0, 0, 0.45);
    color: var(--ink);
  }
  .card--details .brand {
    position: absolute;
    top: 62px;
    left: 0;
    width: 100%;
    padding-left: 90px;
    text-align: center;
  }
  .brand__name {
    font-weight: 800;
    font-size: 30px;
    letter-spacing: 1px;
    line-height: 1.05;
    text-transform: uppercase;
  }
  .brand__sub {
    font-weight: 800;
    font-size: 18px;
    letter-spacing: 1px;
    text-transform: uppercase;
  }
  .contact {
    position: absolute;
    top: 178px;
    left: 0;
    width: 100%;
    padding-left: 90px;
    text-align: center;
    color: var(--ink-soft);
  }
  .contact__name {
    font-weight: 700;
    font-size: 17px;
    letter-spacing: 0.5px;
    text-transform: uppercase;
    color: var(--ink);
    margin-bottom: 4px;
  }
  .contact__line {
    font-weight: 400;
    font-size: 14px;
    line-height: 1.45;
  }
  .card--mark {
    display: flex;
    align-items: center;
    justify-content: center;
  }
  .mark {
    font-weight: 800;
    font-size: 92px;
    letter-spacing: 2px;
    color: var(--ink);
  }
</style>
</head>
<body>
  <main class="sheet">
    <section class="card card--details" aria-label="Card front with contact details">
      <div class="brand">
        <div class="brand__name">Marlowe</div>
        <div class="brand__sub">Group (M.G)</div>
      </div>
      <div class="contact">
        <div class="contact__name">Daniel Marlowe</div>
        <div class="contact__line">0413586207 | danmarl@inboxmail.test</div>
        <div class="contact__line">www.marlowegroup.test</div>
      </div>
    </section>
    <section class="card card--mark" aria-label="Card back with monogram">
      <div class="mark">M.G</div>
    </section>
  </main>
</body>
</html>
```